SaaS Early tech startup business card design

Unique design for experience ecommerce platform company. the business cards will be used by executive members. conformance with color code is required.

```html
<!DOCTYPE html>
<html lang="en">
<head>
<meta charset="utf-8">
<title>nuvel – business card</title>
<link href="https://fonts.googleapis.com/css2?family=Arimo:wght@400;700&display=swap" rel="stylesheet">
<style>
  :root {
    --stage: #e6e8ea;
    --navy: #23233a;
    --teal: #22b39c;
    --teal-blue: #1a8fb0;
    --ink-grey: #6b6b6b;
    --rule: #8a8a8a;
    --white: #ffffff;
  }
  * { box-sizing: border-box; margin: 0; padding: 0; }
  html, body { width: 1200px; height: 900px; overflow: hidden; }
  body {
    background: var(--stage);
    font-family: "Arimo", Arial, sans-serif;
    position: relative;
  }
  .card {
    position: absolute;
    left: 250px;
    width: 700px;
    height: 400px;
    border-radius: 22px;
    overflow: hidden;
    box-shadow: 0 6px 18px rgba(0,0,0,.18);
  }

  /* Front */
  .card-front { top: 30px; background: var(--navy); color: var(--white); }
  .card-front .brand {
    position: absolute; left: 50px; top: 50px;
    font-size: 78px; font-weight: 700; color: var(--teal); letter-spacing: 1px;
  }
  .card-front .stat {
    position: absolute; left: 50px; top: 165px;
    font-size: 66px; font-weight: 400; color: var(--teal);
  }
  .card-front .claim {
    position: absolute; left: 52px; top: 245px;
    font-size: 22px; line-height: 28px; color: var(--white);
  }
  .card-front .pattern-area {
    position: absolute; right: 50px; top: 40px;
    width: 340px; height: 250px;
    border-radius: 40px;
    background: radial-gradient(ellipse at center, rgba(34,179,156,.22), rgba(26,143,176,.08) 60%, rgba(35,35,58,0) 80%);
  }
  .card-front .edge-band {
    position: absolute; left: 0; right: 0; bottom: 0; height: 18px;
    background: linear-gradient(90deg, var(--teal-blue), var(--teal) 60%, #5fd4c0);
  }

  /* Back */
  .card-back { top: 470px; background: var(--white); }
  .card-back .brand {
    position: absolute; right: 60px; top: 40px;
    font-size: 92px; font-weight: 700; color: var(--teal); letter-spacing: 1px;
  }
  .card-back .person { position: absolute; left: 50px; top: 170px; }
  .card-back .person-name { font-size: 30px; font-weight: 700; color: var(--teal); }
  .card-back .person-role { font-size: 20px; color: var(--ink-grey); margin-top: 4px; }
  .card-back .address {
    position: absolute; right: 50px; top: 200px;
    text-align: right; font-size: 20px; line-height: 24px; color: var(--ink-grey);
  }
  .card-back .divider {
    position: absolute; left: 50px; right: 50px; top: 262px;
    height: 1px; background: var(--rule);
  }
  .card-back .contacts {
    position: absolute; left: 50px; top: 278px; list-style: none;
  }
  .card-back .contacts li {
    display: flex; align-items: center; gap: 14px;
    height: 32px; font-size: 22px; color: var(--ink-grey);
  }
  .contact-icon {
    width: 24px; height: 24px; border-radius: 6px; background: var(--teal);
    display: flex; align-items: center; justify-content: center; flex: none;
  }
</style>
</head>
<body>

  <section class="card card-front">
    <div class="brand">nuvel</div>
    <div class="stat">63%</div>
    <p class="claim">Of Consumer Value<br>Privacy Over Popularity<br>When Dealing With<br>Online Platfrom</p>
    <div class="pattern-area" role="img" aria-label="Faint teal line pattern decoration"></div>
    <div class="edge-band"></div>
  </section>

  <section class="card card-back">
    <div class="brand">nuvel</div>
    <div class="person">
      <div class="person-name">Daniel Reyes</div>
      <div class="person-role">Manager</div>
    </div>
    <div class="address">Your address, city<br>state, ZIP 0000</div>
    <div class="divider"></div>
    <ul class="contacts">
      <li>
        <span class="contact-icon">
          <svg width="14" height="14" viewBox="0 0 24 24"><path fill="#fff" d="M6.6 10.8a15 15 0 0 0 6.6 6.6l2.2-2.2c.3-.3.7-.4 1-.2 1.1.4 2.3.6 3.6.6.6 0 1 .4 1 1V20c0 .6-.4 1-1 1A17 17 0 0 1 3 4c0-.6.4-1 1-1h3.5c.6 0 1 .4 1 1 0 1.3.2 2.5.6 3.6.1.3 0 .7-.2 1z"/></svg>
        </span>555-018-2740
      </li>
      <li>
        <span class="contact-icon">
          <svg width="15" height="12" viewBox="0 0 20 14"><rect x="1" y="1" width="18" height="12" fill="none" stroke="#fff" stroke-width="1.8"/><path d="M1 1l9 7 9-7" fill="none" stroke="#fff" stroke-width="1.8"/></svg>
        </span>youremail@mailbox.com
      </li>
      <li>
        <span class="contact-icon">
          <svg width="15" height="15" viewBox="0 0 20 20"><circle cx="10" cy="10" r="8" fill="none" stroke="#fff" stroke-width="1.8"/><path d="M2 10h16M10 2c3 3 3 13 0 16M10 2c-3 3-3 13 0 16" fill="none" stroke="#fff" stroke-width="1.4"/></svg>
        </span>www.yourwebsite.com
      </li>
    </ul>
  </section>

</body>
</html>
```